Business card design for my company.
I would like the card's background colour to be black. You can also see our web site to get an idea of our brand. https://www.tmwhomecrafting.com.au/
- Name
- Email

```html
<!DOCTYPE html>
<html lang="en">
<head>
<meta charset="utf-8">
<title>TMW Home Crafting – Business Card</title>
<link rel="stylesheet" href="https://fonts.googleapis.com/css2?family=Roboto:wght@400;500;700&family=Ubuntu:wght@700&display=swap">
<style>
  :root {
    --bg: #3b3b3b;
    --card-black: #222222;
    --card-white: #f7f7f5;
    --brand-green: #0f9a3e;
    --ink: #1a1a1a;
    --muted-ink: #2c2c2c;
    --soft-white: #e6e6e6;
  }
  * { box-sizing: border-box; margin: 0; padding: 0; }
  html, body { width: 1200px; height: 852px; overflow: hidden; }
  body {
    background: var(--bg);
    font-family: "Roboto", Arial, sans-serif;
    position: relative;
  }
  .card {
    position: absolute;
    top: 276px;
    width: 520px;
    height: 300px;
    border-radius: 18px;
    overflow: hidden;
    box-shadow: 0 6px 0 var(--brand-green);
  }
  .card--front { left: 60px; background: var(--card-black); }
  .card--back  { left: 620px; background: var(--card-white); }

  .brand-name {
    font-family: "Roboto", Arial, sans-serif;
    font-weight: 700;
    letter-spacing: 1px;
    text-transform: uppercase;
    white-space: nowrap;
  }
  .card--front .brand-name {
    position: absolute;
    left: 0; right: 0; top: 108px;
    text-align: center;
    font-size: 34px;
    color: #3a3a3a;
  }
  .card--front .website {
    position: absolute;
    right: 34px; bottom: 26px;
    font-size: 14px;
    color: var(--soft-white);
  }

  .card--back .brand-name {
    position: absolute;
    right: 30px; top: 70px;
    font-size: 24px;
    color: var(--ink);
  }
  .holder { position: absolute; left: 34px; top: 108px; }
  .holder-name {
    font-family: "Ubuntu", Arial, sans-serif;
    font-weight: 700;
    font-size: 24px;
    color: var(--brand-green);
  }
  .holder-role { font-size: 13px; color: var(--muted-ink); margin-top: 2px; }

  .contact-list { position: absolute; left: 34px; top: 196px; list-style: none; }
  .contact-list li {
    display: flex; align-items: center; gap: 10px;
    font-size: 13px; color: var(--muted-ink);
    height: 19px;
  }
  .contact-list svg { width: 12px; height: 12px; fill: var(--brand-green); flex: none; }

  .accent-lines { position: absolute; inset: 0; width: 100%; height: 100%; }
  .accent-lines polyline { fill: none; stroke: var(--brand-green); stroke-width: 3; }
</style>
</head>
<body>

<section class="card card--front" aria-label="Card front">
  <div class="brand-name">TMW Home Crafting</div>
  <div class="website">www.tmwhomecrafting.com.au</div>
</section>

<section class="card card--back" aria-label="Card back">
  <svg class="accent-lines" viewBox="0 0 520 300" aria-hidden="true">
    <polyline points="290,300 440,150 520,150"/>
    <polyline points="310,300 452,160 520,160" style="stroke-width:1.5"/>
  </svg>

  <div class="brand-name">TMW Home Crafting</div>

  <div class="holder">
    <div class="holder-name">Liam Carver</div>
    <div class="holder-role">General Manager</div>
  </div>

  <ul class="contact-list">
    <li>
      <svg viewBox="0 0 24 24"><path d="M6.6 10.8a15.1 15.1 0 0 0 6.6 6.6l2.2-2.2a1 1 0 0 1 1-.25 11.4 11.4 0 0 0 3.6.57 1 1 0 0 1 1 1V20a1 1 0 0 1-1 1A17 17 0 0 1 3 4a1 1 0 0 1 1-1h3.5a1 1 0 0 1 1 1c0 1.25.2 2.45.57 3.57a1 1 0 0 1-.25 1z"/></svg>
      0400 123 456
    </li>
    <li>
      <svg viewBox="0 0 24 24"><path d="M2 5h20v14H2z M2 5l10 8 10-8" /></svg>
      info@tmwhomecrafting.com.au
    </li>
    <li>
      <svg viewBox="0 0 24 24"><circle cx="12" cy="12" r="10"/><path d="M2 12h20M12 2c3 3 3 17 0 20M12 2c-3 3-3 17 0 20" stroke="#f7f7f5" stroke-width="1.5" fill="none"/></svg>
      www.tmwhomecrafting.com.au
    </li>
    <li>
      <svg viewBox="0 0 24 24"><path d="M12 2a7 7 0 0 0-7 7c0 5 7 13 7 13s7-8 7-13a7 7 0 0 0-7-7zm0 9.5A2.5 2.5 0 1 1 12 6.5a2.5 2.5 0 0 1 0 5z"/></svg>
      Riverbend, Tasmania, Australia
    </li>
  </ul>
</section>

</body>
</html>
```